Web Design Project - Shipping Industry

Goals and Objectives
The objective of the new website is to create a more modern look and feel. The site will also allow for a more effective means of communicating with members while providing the public with information and developments in the local, regional and international shipping industry.
Scope
The website will highlight the history of the organisation inclusive of text and photographs. It will take visitors through the years from beginning to present. Information on the history of the shipping industry will also be included.
It will feature current articles on the organisation, its members and stakeholders in the shipping industry. Member information as well as pertinent details regarding the organisation’s subsidiaries will be documented for the website.
Information as it relates to shipping statistics, case studies, laws and regulations, international treaties and trade documents, shipping terms, careers in shipping, job opportunities, training opportunities, information for shippers including port listing and trade lanes will be main features of the content for the website.
The Association’s community involvement, industry calendar events and related links relevant industry members will also be featured.
Target Market
• The General Public;
• Members of the organization;
• Shipping Industry Stakeholders (local, regional and international);
• Tertiary students conducting research.
• Potential employees
• Potential Business Partners
Best Practice Bench Marketing
The following websites are being looked at:
• Korvel Quayworks - http://www.korvelquayworks.example/ (preferred look)
• Tessaly Maritime Association - http://www.tma-freight.example/ (like image transition on main page)
• Drovna - http://www.drovna.example (professional look)
• PLW - http://www.pelworth.example (preferred color: blue in logo)
• Quillo - http://www.quillo.example/electronics/tv-video-audio/ (preferred look for links page: image + short text below + visit site link)
Expected Result
• 3 - 5 pages which must include: [1] main page [2] standard page [3] links page

```html
<!DOCTYPE html>
<html lang="en">
<head>
<meta charset="utf-8">
<title>Meridane Freight</title>
<link rel="stylesheet" href="https://fonts.googleapis.com/css2?family=Arimo:wght@400;700&display=swap">
<style>
:root{
  --navy:#0a0673;
  --navy-deep:#06045a;
  --nav-blue:#1c1a86;
  --accent:#3532b8;
  --grey-text:#8a8a8a;
  --body-text:#333;
  --list-text:#555;
  --band:#f1f1f1;
  --btn:#141266;
}
*{margin:0;padding:0;box-sizing:border-box}
html,body{width:1200px;height:1125px;overflow:hidden;background:#fff;font-family:"Arimo",Arial,sans-serif}
.page{position:relative;width:1200px;height:1125px}
.header{position:absolute;left:0;top:0;width:1200px;height:114px;background:linear-gradient(#0c0a7c,#05035c)}
.brand{position:absolute;left:144px;top:30px;color:#e6e8f4;font-size:28px;font-weight:700;letter-spacing:0}
.login{position:absolute;left:619px;top:32px;display:flex;align-items:center;gap:8px;color:#fff;font-size:12.5px}
.login .label{margin-right:2px}
.login .field{width:138px;height:25px;background:#fff;color:#aaa;font-size:12px;padding:6px 10px}
.login .btn{width:55px;height:26px;background:linear-gradient(#fff,#dcdcdc);border-radius:4px;color:#111;font-size:12px;display:flex;align-items:center;justify-content:center;margin-left:2px}
.nav{position:absolute;left:324px;top:79px;height:35px;display:flex;background:var(--nav-blue);border-radius:4px 4px 0 0;overflow:hidden}
.nav a{color:#d8d9f0;text-decoration:none;font-size:13.5px;letter-spacing:.5px;display:flex;align-items:center;padding:0 19px;border-right:1px solid #2c2a98}
.nav a:last-child{border-right:0}
.nav a.active{background:linear-gradient(#fff,#dcdcdc);color:var(--navy);padding:0 23px}
.hero-band{position:absolute;left:0;top:114px;width:1200px;height:326px;background:linear-gradient(#fff,#efefef)}
.hero{position:absolute;left:141px;top:127px;width:919px;height:299px;border:1px solid #cfd3dc;background:linear-gradient(#dfe5f0 0%,#e9edf5 30%,#8c98b4 70%,#5f6e92 100%)}
.card{position:absolute;top:454px;width:278px}
.card .photo{height:147px;background:#e8e8e8;padding:8px}
.card .photo div{width:100%;height:100%}
.card .body{height:147px;background:linear-gradient(#fff,#e6e6e6);border-bottom:2px solid var(--navy);padding:12px 24px 0 10px}
.title{color:var(--accent);font-weight:700;font-size:23px;line-height:24px}
.title span{display:block;color:var(--grey-text);font-weight:400;font-size:19px;line-height:21px}
.card p{font-size:13px;line-height:17px;color:var(--body-text);margin-top:6px;padding-left:2px}
.more{position:absolute;right:0;top:294px;width:78px;height:26px;background:var(--btn);color:#d8d9f0;font-size:10.5px;letter-spacing:.6px;display:flex;align-items:center;justify-content:center}
.services{position:absolute;left:781px;top:454px;width:278px;height:292px;background:linear-gradient(#fff,#e8e8e8);border-bottom:2px solid var(--navy);padding:14px 17px}
.services .title{font-size:23px}
.services .title span{display:inline;font-size:20px}
.services .lead{font-size:13px;line-height:17px;color:var(--body-text);margin:6px 0 4px 11px}
.services ul{list-style:none}
.services li,.col li{font-size:12.5px;color:var(--list-text);height:22.5px;line-height:22.5px}
.services li{padding-left:11px;position:relative}
.services li::before{content:"";position:absolute;left:0;top:8px;border:3px solid transparent;border-left:4px solid #bbb}
.rule{position:absolute;left:141px;top:795px;width:919px;height:1px;background:#e0e0e0}
.col{position:absolute;top:811px}
.col h2{color:var(--accent);font-size:23px;font-weight:700;margin-bottom:18px}
.col ul{list-style:none;padding-left:2px}
.map{position:absolute;left:806px;top:858px;width:183px;height:84px;background:radial-gradient(ellipse at center,#9a9a9a 0%,#b8b8b8 55%,#fff 75%)}
.partners{position:absolute;left:0;top:965px;width:1200px;height:101px;background:var(--band);display:flex;align-items:center;padding-left:160px}
.partners div{width:152px;color:#8d8d8d;font-size:15px;font-weight:700;display:flex;align-items:center;gap:6px}
.partners i{width:12px;height:12px;background:#a5a5a5;display:inline-block}
.footer{position:absolute;left:0;top:1066px;width:1200px;height:59px;background:var(--navy-deep);color:#c9cae6;font-size:10.5px;display:flex;align-items:center;justify-content:center;letter-spacing:.3px}
</style>
</head>
<body>
<div class="page">
  <header class="header">
    <div class="brand">Meridane Freight</div>
    <div class="login"><span class="label">Member Log in</span><span class="field">Username</span><span class="field">********</span><span class="btn">LOGIN</span></div>
    <nav class="nav">
      <a class="active">HOME</a><a>ABOUT US</a><a>CAPABILITIES</a><a>NEWS</a><a>SERVICES</a><a>CAREERS</a><a>CONTACT US</a>
    </nav>
  </header>
  <div class="hero-band"></div>
  <div class="hero" role="img" aria-label="Large container ship on calm blue water"></div>

  <section class="card" style="left:141px">
    <div class="photo"><div role="img" aria-label="Container ship sailing at sea" style="background:linear-gradient(135deg,#1f6b70,#3a8a8a 50%,#17555a)"></div></div>
    <div class="body">
      <div class="title">PERFORMANCE<span>REDEFINED</span></div>
      <p>Lorem ipsum dolor sit amet conse ctetur adipi sicing elit, sed do eiusmod tempor incididunt ut labore et dolore magna aliqua.</p>
    </div>
    <div class="more">READ MORE</div>
  </section>

  <section class="card" style="left:459px">
    <div class="photo"><div role="img" aria-label="Port cranes lit at dusk over the harbour" style="background:linear-gradient(#2c3550,#8a6a55 45%,#3a3a40 60%,#6a5a3a)"></div></div>
    <div class="body">
      <div class="title">ABOUT<span>OUR COMPANY</span></div>
      <p>Lorem ipsum dolor sit amet conse ctetur adipi sicing elit, sed do eiusmod tempor incididunt ut labore et dolore magna aliqua.</p>
    </div>
    <div class="more">READ MORE</div>
  </section>

  <section class="services">
    <div class="title">OUR <span>SERVICES</span></div>
    <p class="lead">Lorem ipsum dolor sit amet conse ctetur adipi sicing elit, sed do eiusmod</p>
    <ul>
      <li>Lorem ipsum dolor sit amet conse</li>
      <li>Adipisicing elit, sed do eiusmod</li>
      <li>Tempor incididunt ut labore et dolore</li>
      <li>Aliqua enim ad minim</li>
      <li>Veniam, quis nostrud exercitation</li>
      <li>Ipsum dolor sit amet conse</li>
      <li>Adipisicing elit, sed do eiusmod</li>
      <li>Incididunt ut labore et dolore</li>
      <li>Magna aliqua enim ad minim</li>
    </ul>
    <div class="more" style="top:292px">READ MORE</div>
  </section>

  <div class="rule"></div>

  <section class="col" style="left:150px">
    <h2>INFORMATION</h2>
    <ul><li>Lorem ipsum dolor sit amet conse</li><li>Adipisicing elit, sed do eiusmod</li><li>Tempor incididunt ut labore et dolore</li><li>Aliqua enim ad minim.</li></ul>
  </section>
  <section class="col" style="left:470px">
    <h2>WHY BUY FROM US</h2>
    <ul style="padding-left:3px"><li>Lorem ipsum dolor sit amet conse</li><li>Adipisicing elit, sed do eiusmod</li><li>Tempor incididunt ut labore et dolore</li><li>Aliqua enim ad minim.</li></ul>
  </section>
  <section class="col" style="left:796px">
    <h2>OUR LOCATIONS</h2>
  </section>
  <div class="map" role="img" aria-label="Grey world map showing office locations"></div>

  <div class="partners">
    <div><i></i>Brevik Marine</div>
    <div><i></i>Calder Wharves</div>
    <div><i></i>Ostra Cargo</div>
    <div><i></i>Velmar Line</div>
    <div><i></i>Tidecargo</div>
    <div><i></i>Quay Data</div>
  </div>

  <footer class="footer">© 2012 Meridane Freight. All Rights Reserved.</footer>
</div>
</body>
</html>
```